A website where experts collaborate on your project

I am building a new website where experts (yes, like designers) collaborate on projects with the project owner. More minds = more collaboration = better end product. Please see Pelmora(dot)com for a quick landing page I created for collaborating on presentations (although there will be many project types offered)

I am looking for a DESIGNER LONG TERM, but for now, just need initial mock ups to show the web programmers.

I have 21 Word documents loosely designed, what I would like to see here is a theme. Please DO NOT GO OFF WHAT YOU CURRENTLY SEE AT PELMORA. What is up now is only a quick landing page.

You can view a Word doc of the homepage here:
https://www.filevanta.com/s/qx83kdm2/home.docx?dl=0

WHAT AM I LOOKING FOR?
A clean, well designed theme.

Here is a link to the logo:
https://www.filevanta.com/s/mr47tpz9/logo%20-%20horizontal.tif?dl=0
-----------------------------------------
Here are a few sites I like the design of and what I like about them:
www.quenbrook.com-all around my favorite, beautiful graphics, clean layout, bold use of colors on a dark background
Ravelto.com- clean layout, The use of humans and bubble style elements.
Mintharbor.com :) clean, bold, unique pop art style but professional
plumevault.com - From the unique colors and artwork and the ability of that art to not interfere with the important elements of the site
sparkwidgets.com-clean, nice colors, well organized and separated sections.
www.dunmereco.com-love the font, use of colors and sectionalized style

All in all, I am not picky and open to so many styles. I would ultimately like the designer I pick to design all 21 pages.
Updates

Hello everyone,Moving forward, I would like you all to pay special attention to the section in my brief titled "Here are a few sites I like the design of and what I like about them". Please see below, I handpicked each one of these as sites I really like. Thank you.Here are a few sites I like the design of and what I like about them:Ravelto.com- clean layout, The use of humans and bubble style elements.Mintharbor.com :) clean, bold, unique pop art style but professionalwriteraccess.com - From the unique colors and artwork and the ability of that art to not interfere with the important elements of the sitegrowthgeeks.com-clean, nice colors, well organized and separated sections.www.dunmereco.com-love the font, use of colors and sectionalized stylewww.quenbrook.com-beautiful graphics, clean layout, bold use of colors----------------------------------------- Added Tuesday, November 24, 2015

I updated the homepage, you can see it here:https://www.dropbox.com/s/kwlkbsookq3cg2m/1new%20homepage.docx?dl=0I am modeling it after my favorite designed site: triplelift.comI love the dark colors with the orange glowing style boldness of the buttons. It's real clean too. Added Tuesday, November 24, 2015

Target Market(s)

small business owners, marketers, freelancer writers, graphic designers,

Industry/Entity Type

Building

Number of Pages Required

5+ page

Requirements
Must have
• I can't think of anything the project must have.
Nice to have
• WHAT AM I LOOKING FOR?
• A clean, well designed theme. I had a designer do a bit of work putting elements together, I found it to be very plain, but I like the Application Page (https://www.filevanta.com/s/jb19ckr3/Pelmora-Website.ai?dl=0)
• Here is a link to the logo:
• https://www.filevanta.com/s/mr47tpz9/logo%20-%20horizontal.tif?dl=0
• Here are a few sites I like the design of and what I like about them:
• Ravelto.com- clean layout, The use of humans and bubble style elements.
• Mintharbor.com :) clean, bold, unique pop art style but professional
• plumevault.com - From the unique colors and artwork and the ability of that art to not interfere with the important elements of the site
• sparkwidgets.com-clean, nice colors, well organized and separated sections.
• www.dunmereco.com-love the font, use of colors and sectionalized style
• www.quenbrook.com-beautiful graphics, clean layout, bold use of colors
• -----------------------------------------
Should not have
• out of the boxed, templated style website. I want this site to be memorable and not look like a thousand others

```html
<!DOCTYPE html>
<html lang="en">
<head>
<meta charset="utf-8">
<title>Pelmora – Crowd Projects</title>
<link href="https://fonts.googleapis.com/css2?family=Open+Sans:ital,wght@0,400;0,600;0,700;1,400&family=Raleway:wght@500;600;700;800&display=swap" rel="stylesheet">
<style>
:root{
  --orange:#f7941d;
  --blue:#4aaecb;
  --blue-dark:#3a9bb8;
  --red:#e63b2e;
  --ink:#444;
  --muted:#777;
  --line:#e2e2e2;
  --panel-head:#ececec;
  --hero-grey:#e9e9ec;
  --footer:#333;
}
*{box-sizing:border-box;margin:0;padding:0}
html,body{width:1200px;height:2206px;overflow:hidden}
body{position:relative;background:#fff;font-family:"Open Sans",Arial,sans-serif;color:var(--ink)}
.abs{position:absolute}
.topline{left:0;top:0;width:1200px;height:4px;background:var(--orange)}

/* header */
.brand{left:98px;top:58px;display:flex;align-items:center;gap:10px}
.brand-name{font-family:"Raleway",sans-serif;font-weight:700;font-size:26px;color:var(--orange)}
.brand-dot{width:34px;height:34px;border-radius:50%;background:var(--orange)}
.bubble{left:500px;top:20px;width:232px;height:54px}
.bubble-text{left:520px;top:33px;width:192px;text-align:center;font-size:9.5px;line-height:13px;color:#666}
.nav{left:474px;top:86px;display:flex;align-items:center;font-size:13px;color:#555}
.nav .help{width:16px;height:16px;border-radius:50%;background:var(--blue);color:#fff;font-size:11px;font-weight:700;text-align:center;line-height:16px;margin-right:22px}
.nav a{color:#555;text-decoration:none;margin-right:38px}
.browse-label{left:899px;top:49px;font-size:12.5px;color:#555}
.browse-select{left:899px;top:72px;width:202px;height:34px;border:1px solid #ccc;background:#fff;box-shadow:inset 0 1px 2px rgba(0,0,0,.08)}
.browse-select .arrow{position:absolute;right:0;top:0;width:36px;height:32px;border-left:1px solid #ccc;background:linear-gradient(#f7f7f7,#e3e3e3)}
.browse-select .arrow:after{content:"";position:absolute;left:13px;top:13px;border:5px solid transparent;border-top:6px solid #888}

/* hero */
.hero{left:0;top:137px;width:1200px;height:462px;overflow:hidden}
.hero-photo{left:566px;top:146px;width:634px;height:453px}
.hero-title{left:98px;top:298px;font-family:"Raleway",sans-serif;font-weight:800;font-size:37px;color:#fff;letter-spacing:.3px}
.hero-sub{left:99px;top:344px;font-family:"Raleway",sans-serif;font-size:18px;color:#fff}
.btn-start{left:98px;top:387px;width:133px;height:44px;border-radius:3px;background:linear-gradient(#fbfbfb,#dcdcdc);box-shadow:0 2px 3px rgba(0,0,0,.25);font-family:"Raleway",sans-serif;font-weight:700;font-size:14px;color:#333;text-align:center;line-height:44px}
.dots{left:98px;top:549px;display:flex;gap:4px}
.dots i{width:14px;height:14px;border-radius:50%;background:#bbb;display:block}
.dots i.on{background:var(--orange)}

/* panels */
.panel{border:1px solid var(--line);background:#fff}
.panel-head{height:40px;background:var(--panel-head);font-family:"Raleway",sans-serif;font-weight:700;font-size:15.5px;color:#333;padding-left:18px;line-height:40px;letter-spacing:.3px}
.filter{left:97px;top:641px;width:287px;height:1124px}
.f-title{position:absolute;left:52px;font-family:"Raleway",sans-serif;font-weight:600;font-size:14.5px;color:#444}
.f-icon{position:absolute;left:18px;width:18px;height:18px}
.f-list{position:absolute;left:45px;font-size:11.5px;color:#555;list-style:none;line-height:25px}
.f-rule{position:absolute;left:0;width:285px;height:1px;background:var(--line)}
.caret{position:absolute;right:27px;border:5px solid transparent;border-top:6px solid #999}
.track{left:40px;top:101px;width:222px;height:5px;background:#e4e4e4;border-radius:3px}
.track-fill{left:50px;top:101px;width:121px;height:5px;background:var(--blue)}
.knob{width:24px;height:24px;border-radius:50%;background:var(--blue);border:3px solid #d7eef5;box-shadow:0 0 0 1px var(--blue-dark)}
.range-lbl{font-size:11px;color:#555}
.btn-save{left:24px;top:970px;width:241px;height:46px;border-radius:3px;background:linear-gradient(#5cc0dc,#3a9bb8);box-shadow:0 2px 3px rgba(0,0,0,.25);color:#fff;font-family:"Raleway",sans-serif;font-weight:700;font-size:14.5px;text-align:center;line-height:46px}

.projects{left:424px;top:641px;width:677px;height:1124px}
.sort{position:absolute;right:28px;top:0;font-size:12px;color:#777;line-height:40px}
.sort b{color:var(--blue);font-weight:600}
.item{position:absolute;left:0;width:675px;height:201px;border-bottom:1px solid var(--line)}
.thumb{position:absolute;left:19px;top:22px;width:176px;height:158px;border:1px solid #ddd;padding:4px;background:#fff}
.thumb div{width:100%;height:100%}
.item h3{position:absolute;left:221px;top:24px;font-family:"Raleway",sans-serif;font-weight:600;font-size:15.5px;color:#333}
.item p{position:absolute;left:221px;top:55px;width:430px;font-size:11.3px;line-height:21px;color:#666}
.price{position:absolute;left:221px;top:102px;font-family:"Raleway",sans-serif;font-weight:800;font-size:25px;color:var(--red)}
.loc{position:absolute;left:221px;top:138px;font-size:12px;color:#555}
.time{position:absolute;right:20px;top:166px;font-size:11.5px;color:#555}
.pager{position:absolute;left:19px;top:1076px;display:flex;gap:10px}
.pager span{height:24px;min-width:24px;padding:0 8px;border:1px solid #ddd;background:linear-gradient(#fff,#eee);font-size:11px;color:#444;line-height:22px;text-align:center}
.pager span.on{background:var(--blue);border-color:var(--blue);color:#fff}
.pager span.wide{padding:0 13px}

/* testimonials */
.testi{left:0;top:1815px;width:1200px;height:244px;background:var(--orange)}
.testi h2{position:absolute;left:0;width:1200px;top:36px;text-align:center;font-family:"Raleway",sans-serif;font-weight:700;font-size:20px;color:#fff;letter-spacing:.5px}
.testi q{position:absolute;left:300px;width:600px;top:77px;text-align:center;font-style:italic;font-size:13.5px;line-height:25px;color:#fff;quotes:none;display:block}
.avatar{left:508px;top:142px;width:72px;height:72px;border-radius:50%;border:3px solid #fff;background:radial-gradient(circle at 50% 40%,#e6c9b4,#a8a8a8)}
.who{left:598px;top:155px;color:#fff}
.who b{display:block;font-family:"Raleway",sans-serif;font-weight:600;font-size:16px}
.who i{font-size:12px}
.chev{top:98px;width:14px;height:24px}

/* footer */
.footer{left:0;top:2059px;width:1200px;height:147px;background:var(--footer);color:#fff}
.social{position:absolute;left:494px;top:26px;display:flex;gap:7px}
.social i{width:36px;height:36px;border:2px solid #fff;border-radius:50%;display:block}
.f-links{position:absolute;left:0;width:1200px;top:80px;text-align:center;font-size:12px}
.f-copy{position:absolute;left:0;width:1200px;top:107px;text-align:center;font-size:11.5px}
</style>
</head>
<body>

<div class="abs topline"></div>

<header>
  <div class="abs brand"><span class="brand-name">Pelmora</span><span class="brand-dot"></span></div>
  <svg class="abs bubble" viewBox="0 0 232 54"><path d="M116 2C52 2 6 11 6 25c0 12 28 20 70 22L0 53l94-5c7 .3 14 .4 22 .4 64 0 110-10 110-23S180 2 116 2z" fill="#fff" stroke="#bbb" stroke-width="1.2"/></svg>
  <div class="abs bubble-text">At vero eos et accusamus et iusto odio dii ssimos ducimus qui</div>
  <nav class="abs nav"><span class="help">?</span><a>Projects</a><a>How It Works</a><a>Plans</a><a>My Account</a></nav>
  <div class="abs browse-label">Browse By</div>
  <div class="abs browse-select"><span class="arrow"></span></div>
</header>

<section class="abs hero">
  <svg width="1200" height="462" class="abs" style="left:0;top:0">
    <defs>
      <linearGradient id="heroBlue" x1="0" y1="0" x2="0" y2="1"><stop offset="0" stop-color="#54b3cf"/><stop offset="1" stop-color="#4aa7c3"/></linearGradient>
      <linearGradient id="heroFloor" x1="0" y1="0" x2="0" y2="1"><stop offset="0" stop-color="#eaeaea"/><stop offset="1" stop-color="#fafafa"/></linearGradient>
    </defs>
    <rect width="1200" height="462" fill="var(--hero-grey)"/>
    <polygon points="0,0 866,0 600,380 0,380" fill="url(#heroBlue)"/>
    <polygon points="1200,120 1200,380 1130,380" fill="url(#heroBlue)"/>
    <rect y="380" width="1200" height="82" fill="url(#heroFloor)"/>
  </svg>
  <div class="abs hero-photo" role="img" aria-label="Smiling businessman in a suit working on a laptop with a design on screen" style="left:566px;top:9px;background:radial-gradient(ellipse at 68% 40%,#3a4257 0%,#4b5468 35%,rgba(200,200,205,.6) 65%,rgba(233,233,236,0) 80%)"></div>
  <div class="abs hero-title" style="top:161px">CONVERT MORE CUSTOMERS</div>
  <div class="abs hero-sub" style="top:207px">Experience the power of experts collaborating on your project</div>
  <div class="abs btn-start" style="top:250px">GET STARTED</div>
  <div class="abs dots" style="top:412px"><i class="on"></i><i></i><i></i><i></i></div>
</section>

<aside class="abs panel filter">
  <div class="panel-head">FILTER</div>
  <svg class="f-icon" style="top:58px" viewBox="0 0 18 18"><text x="4" y="15" font-family="Open Sans" font-weight="700" font-size="17" fill="#f7941d">$</text></svg>
  <div class="f-title" style="top:58px">Price</div>
  <div class="abs track"></div><div class="abs track-fill"></div>
  <div class="abs knob" style="left:38px;top:91px"></div>
  <div class="abs knob" style="left:159px;top:91px"></div>
  <div class="abs range-lbl" style="left:40px;top:118px">$20</div>
  <div class="abs range-lbl" style="right:24px;top:118px">$1,000+</div>
  <div class="f-rule" style="top:158px"></div>

  <svg class="f-icon" style="top:181px" viewBox="0 0 18 18"><circle cx="9" cy="9" r="8" fill="#f7941d"/><path d="M4 6c2 0 3 1 3 3s2 2 2 4M12 3c0 2 1 3 3 3" stroke="#fff" stroke-width="1.5" fill="none"/></svg>
  <div class="f-title" style="top:180px">Country</div>
  <ul class="f-list" style="top:209px"><li>U.K</li><li>U.S</li><li>Spain</li><li>Australia</li><li>England</li><li>South Africa</li><li>India</li></ul>
  <div class="f-rule" style="top:397px"></div>

  <svg class="f-icon" style="top:420px" viewBox="0 0 18 18"><rect y="3" width="18" height="2.5" fill="#f7941d"/><rect y="8" width="18" height="2.5" fill="#f7941d"/><rect y="13" width="18" height="2.5" fill="#f7941d"/></svg>
  <div class="f-title" style="top:418px">Categories</div>
  <ul class="f-list" style="top:447px"><li>All Categories</li><li>Inbound Content</li><li>Content Marketing</li><li>Graphic Designer</li><li>Lead Generations</li><li>Email Marketing</li><li>Conversations</li><li>Social Media</li><li>Copywriter</li></ul>
  <div class="f-rule" style="top:686px"></div>

  <svg class="f-icon" style="top:703px" viewBox="0 0 18 18"><circle cx="9" cy="9" r="7.5" fill="none" stroke="#f7941d" stroke-width="2"/><path d="M9 4.5V9h3.5" stroke="#f7941d" stroke-width="2" fill="none"/></svg>
  <div class="f-title" style="top:701px">Time Left</div><span class="caret" style="top:709px"></span>
  <div class="f-rule" style="top:737px"></div>

  <svg class="f-icon" style="top:754px" viewBox="0 0 18 18"><path d="M5 4.5a6.5 6.5 0 1 0 8 0" stroke="#f7941d" stroke-width="2.2" fill="none"/><path d="M9 1v8" stroke="#f7941d" stroke-width="2.2"/></svg>
  <div class="f-title" style="top:752px">Active | Expired</div><span class="caret" style="top:760px"></span>
  <div class="f-rule" style="top:789px"></div>

  <svg class="f-icon" style="top:806px" viewBox="0 0 18 18"><circle cx="9" cy="5" r="4" fill="#f7941d"/><path d="M2 18c0-5 3-8 7-8s7 3 7 8z" fill="#f7941d"/></svg>
  <div class="f-title" style="top:804px">Contains adult content</div><span class="caret" style="top:812px"></span>
  <div class="f-rule" style="top:840px"></div>

  <svg class="f-icon" style="top:857px" viewBox="0 0 18 18"><circle cx="6" cy="6" r="4.5" fill="none" stroke="#f7941d" stroke-width="2.2"/><path d="M9 9l7 7M13 13l-2 2M15 15l-2 2" stroke="#f7941d" stroke-width="2.2"/></svg>
  <div class="f-title" style="top:855px">Keywords</div><span class="caret" style="top:863px"></span>
  <div class="f-rule" style="top:892px"></div>

  <svg class="f-icon" style="top:908px" viewBox="0 0 18 18"><circle cx="5" cy="5" r="3" fill="#f7941d"/><circle cx="13" cy="5" r="3" fill="#f7941d"/><path d="M0 15c0-4 2-6 5-6s5 2 5 6zM8 15c0-4 2-6 5-6s5 2 5 6z" fill="#f7941d"/></svg>
  <div class="f-title" style="top:906px">Followers</div><span class="caret" style="top:914px"></span>
  <div class="f-rule" style="top:943px"></div>

  <div class="abs btn-save">SAVE FILTER</div>
</aside>

<main class="abs panel projects">
  <div class="panel-head">CROWD PROJECTS</div>
  <div class="sort">Sort By :&nbsp;&nbsp; <b>Price</b> | country | Time left</div>

  <article class="item" style="top:40px">
    <div class="thumb"><div role="img" aria-label="Audience seated at a conference presentation" style="background:linear-gradient(160deg,#c79a62,#8c6a4a 50%,#5d6b7d)"></div></div>
    <h3>Morbi in ante arcu. Maecenas sit amet sem vel</h3>
    <p>At vero eos et accusamus et iusto odio dignissimos ducimus qui blanditiis praesentium voluptatum deleniti atque corrupti qu..</p>
    <div class="price">$80</div><div class="loc">Location&nbsp; : &nbsp;U.K.</div><div class="time">Time Left: 6 days</div>
  </article>

  <article class="item" style="top:241px">
    <div class="thumb"><div role="img" aria-label="Business team reviewing plans around a white table" style="background:linear-gradient(160deg,#eef1f4,#c4ccd6 55%,#8a97a8)"></div></div>
    <h3>Lorem ipsum dolor sit amet, consectetur adipiscing elit</h3>
    <p>At vero eos et accusamus et iusto odio dignissimos ducimus qui blanditiis praesentium voluptatum deleniti atque corrupti qu..</p>
    <div class="price">$80</div><div class="loc">Location&nbsp; : &nbsp;CA.</div><div class="time">Time Left: 6 days</div>
  </article>

  <article class="item" style="top:442px">
    <div class="thumb"><div role="img" aria-label="Colleagues in colourful clothing meeting with laptops" style="background:linear-gradient(160deg,#7aa04a,#c98a3a 45%,#3d6fa8)"></div></div>
    <h3>Nemo enim ipsam voluptatem quia voluptas sit aspern</h3>
    <p>At vero eos et accusamus et iusto odio dignissimos ducimus qui blanditiis praesentium voluptatum deleniti atque corrupti qu..</p>
    <div class="price">$250</div><div class="loc">Location&nbsp; : &nbsp;U.K.</div><div class="time">Time Left: 6 days</div>
  </article>

  <article class="item" style="top:643px">
    <div class="thumb"><div role="img" aria-label="Two women working together on a laptop" style="background:linear-gradient(160deg,#d9d9d9,#6d6d6d 50%,#2a2a2a)"></div></div>
    <h3>Duis aute irure dolor in reprehenderit in voluptate</h3>
    <p>At vero eos et accusamus et iusto odio dignissimos ducimus qui blanditiis praesentium voluptatum deleniti atque corrupti qu..</p>
    <div class="price">$62</div><div class="loc">Location&nbsp; : &nbsp;U.K.</div><div class="time">Time Left: 6 days</div>
  </article>

  <article class="item" style="top:844px">
    <div class="thumb"><div role="img" aria-label="Team gathered around a tablet in a bright office" style="background:linear-gradient(160deg,#dfe9f2,#9fb6cc 55%,#4f6d8c)"></div></div>
    <h3>Dam libero tempore, cum soluta nobis est eligendi optio</h3>
    <p>At vero eos et accusamus et iusto odio dignissimos ducimus qui blanditiis praesentium voluptatum deleniti atque corrupti qu..</p>
    <div class="price">$48</div><div class="loc">Location&nbsp; : &nbsp;U.K.</div><div class="time">Time Left: 6 days</div>
  </article>

  <div class="pager"><span class="wide">Prev</span><span class="on">1</span><span>2</span><span>3</span><span>4</span><span>5</span><span>6</span><span>..</span><span>22</span><span class="wide">Next</span></div>
</main>

<section class="abs testi">
  <h2>TESTIMONIALS</h2>
  <q>“With Pelmora I have multiple experts perfecting my content and I only pay for the feedback I find valuable. It's perfect”</q>
  <div class="abs avatar" role="img" aria-label="Portrait of the quoted client"></div>
  <div class="abs who"><b>Dale Morrow</b><i>( CEO, Vantel 9 )</i></div>
  <svg class="abs chev" style="left:97px" viewBox="0 0 14 24"><path d="M12 2L2 12l10 10" stroke="#fff" stroke-opacity=".7" stroke-width="2" fill="none"/></svg>
  <svg class="abs chev" style="left:1088px" viewBox="0 0 14 24"><path d="M2 2l10 10L2 22" stroke="#fff" stroke-opacity=".7" stroke-width="2" fill="none"/></svg>
</section>

<footer class="abs footer">
  <div class="social"><i></i><i></i><i></i><i></i><i></i></div>
  <div class="f-links">Home &nbsp;| &nbsp;Projects &nbsp;| &nbsp;How It Works &nbsp;| &nbsp;Plans &nbsp;| &nbsp;My Account</div>
  <div class="f-copy">© Pelmora. 2015. All rights reserved. Site Map &nbsp;| Privacy &nbsp;| Security &nbsp;| Disclaimer</div>
</footer>

</body>
</html>
```